Wordpress Design Project

Need a page like this but with your own personal twist

I will provide you the iframed form on 2nd page

http://www.brightpolicysaver.example/index1178.php?subid=8715815

Requirements
Must have
• Article with link out
must pass zipcode to iframed form on 2nd page.

Must provide css for form pages.

```html
<!DOCTYPE html>
<html lang="en">
<head>
<meta charset="utf-8">
<title>BrightPolicySaver – Save Big on Your Car Insurance</title>
<link rel="stylesheet" href="https://fonts.googleapis.com/css2?family=Oswald:wght@500;700&family=Oxygen:wght@400;700&family=Roboto+Condensed:wght@400;700&family=Archivo+Black&family=Ubuntu:wght@500&display=swap">
<style>
:root{
  --navy:#062c5b;
  --navy-deep:#0b2a55;
  --ink:#0f2c59;
  --red:#d9262b;
  --red-dark:#a8161b;
  --yellow:#ffd514;
  --white:#ffffff;
  --frame:#dfe3e6;
  --zip-grey:#d3d8db;
  --footer-grey:#e4e6e8;
  --footer-dark:#0b1220;
  --muted:#6f7680;
  --text:#1d1d1d;
}
*{box-sizing:border-box;margin:0;padding:0}
html,body{width:1200px;height:951px;overflow:hidden}
body{position:relative;background:var(--white);font-family:"Oxygen",Arial,sans-serif;color:var(--text)}

.site-header{position:absolute;left:0;top:0;width:1200px;height:128px;border-top:4px solid var(--navy-deep);
  background:linear-gradient(#fff 0,#fff 55%,#eceef0 100%)}
.brand{position:absolute;left:135px;top:40px;font-family:"Ubuntu",sans-serif;font-weight:500;font-size:36px;color:var(--ink);display:flex;align-items:center;gap:12px}
.brand-dot{width:16px;height:16px;background:var(--red);border-radius:50%}
.helpline{position:absolute;left:871px;top:28px;font-family:"Roboto Condensed",sans-serif;color:var(--ink)}
.helpline-label{font-size:22px;display:block}
.helpline-number{font-size:31px;font-weight:700;display:block;margin-top:4px;letter-spacing:.3px}

.hero-band{position:absolute;left:0;top:128px;width:1200px;height:594px;background:var(--navy)}
.hero-frame{position:absolute;left:128px;top:30px;width:944px;height:535px;background:var(--frame)}
.hero-scene{position:absolute;left:13px;top:12px;width:919px;height:511px;
  background:linear-gradient(180deg,#0c3e86 0%,#1f5ea8 45%,#5f9fd0 62%,#1b86b8 72%,#2aa3c9 80%,#c8aa7d 92%,#b89060 100%)}
.car-area{position:absolute;left:30px;top:300px;width:420px;height:210px;border-radius:40px 60px 20px 20px;
  background:linear-gradient(180deg,#c4161c,#8e0e12)}
.hero-copy{position:absolute;left:50px;top:25px;color:var(--white)}
.price-line{font-family:"Oswald",sans-serif;font-weight:700;color:var(--yellow);font-size:30px;line-height:1}
.price-line strong{font-size:54px}
.hero-copy p{font-size:34px;line-height:40px;margin-top:10px;width:330px}

.quote-panel{position:absolute;left:555px;top:12px;width:463px;height:528px;background:var(--white);border-radius:0 0 10px 10px}
.panel-tab{position:absolute;top:12px;width:20px;height:18px;background:var(--red);border-radius:8px 8px 0 0}
.panel-title{text-align:center;font-family:"Oswald",sans-serif;font-weight:700;line-height:1}
.panel-title .big{display:block;color:var(--red);font-size:44px;margin-top:8px}
.panel-title .sub{display:block;color:var(--ink);font-size:34px;margin-top:4px}
.steps{position:absolute;top:100px;left:0;width:463px}
.step{position:absolute;width:130px;text-align:center;font-size:16px;line-height:20px;color:#333}
.step svg{display:block;margin:0 auto 4px}
.step .save{color:var(--red)}
.zip-box{position:absolute;left:28px;top:272px;width:402px;height:95px}
.zip-label{position:absolute;left:68px;top:0;width:268px;text-align:center;font-size:17px;padding-top:12px;color:#333}
.zip-input{position:absolute;left:88px;top:49px;width:230px;height:30px;border:1px solid #8a8f94;border-radius:7px;background:#fff}
.continue-btn{position:absolute;left:132px;top:368px;width:200px;height:48px;border:0;border-radius:0 0 8px 8px;
  background:linear-gradient(#e0262b,var(--red-dark));color:#fff;font-family:"Archivo Black",sans-serif;font-size:25px;
  display:flex;align-items:center;justify-content:center;gap:12px}
.secure-note{position:absolute;left:0;width:463px;top:425px;text-align:center;font-family:"Courier New",monospace;font-size:11px;color:#444}
.trust-badge{position:absolute;left:167px;top:456px;width:133px;height:46px;border-radius:4px;background:#e9ebed}

.legal{position:absolute;left:0;top:722px;width:1200px;height:150px;background:var(--footer-grey);font-family:Arial,sans-serif;font-size:11px;line-height:13px;color:#111}
.legal p{position:absolute;left:137px;width:920px}

.site-footer{position:absolute;left:0;top:872px;width:1200px;height:79px;background:var(--footer-dark);font-family:Arial,sans-serif;font-size:11px;color:var(--muted)}
.footer-links{position:absolute;left:137px;top:24px;line-height:13px}
.footer-links a{color:var(--muted);text-decoration:none}
.footer-badge{position:absolute;left:960px;top:30px;width:111px;height:20px;background:#fff;border:1px solid #777}
</style>
</head>
<body>
<header class="site-header">
  <div class="brand"><span class="brand-dot"></span>BrightPolicySaver</div>
  <div class="helpline"><span class="helpline-label">Need help Call us:</span><span class="helpline-number">1-800-555-0142</span></div>
</header>

<section class="hero-band">
  <div class="hero-frame">
    <div class="hero-scene" role="img" aria-label="Red hatchback car parked on a beach under a blue sky with the sea behind">
      <div class="car-area"></div>
    </div>
    <div class="hero-copy" style="left:50px;top:40px">
      <div class="price-line">AS low as <strong>$7/week</strong></div>
      <p>Over 300,000 people have used our site to help find &amp; compare discount car insurance rates!</p>
    </div>
  </div>

  <span class="panel-tab" style="left:536px"></span>
  <span class="panel-tab" style="left:1019px"></span>

  <div class="quote-panel" style="top:12px">
    <h1 class="panel-title"><span class="big">Save Big!</span><span class="sub">on Your Car Insurance</span></h1>
    <div class="steps">
      <div class="step" style="left:14px">
        <svg width="118" height="108" viewBox="0 0 118 108"><circle cx="54" cy="54" r="51" fill="#fff" stroke="#d9262b" stroke-width="2"/><path d="M54 3 A51 51 0 0 1 104 44" fill="none" stroke="#d9262b" stroke-width="9"/><path d="M92 42 L116 42 L103 66 Z" fill="#d9262b"/><text x="54" y="50" text-anchor="middle" font-family="Archivo Black,sans-serif" font-size="25" fill="#0f2c59">Step</text><text x="54" y="82" text-anchor="middle" font-family="Archivo Black,sans-serif" font-size="25" fill="#0f2c59">1</text></svg>
        Enter your zip code.
      </div>
      <div class="step" style="left:163px;width:160px;margin-left:-15px">
        <svg width="118" height="108" viewBox="0 0 118 108"><circle cx="54" cy="54" r="51" fill="#fff" stroke="#d9262b" stroke-width="2"/><path d="M54 3 A51 51 0 0 1 104 44" fill="none" stroke="#d9262b" stroke-width="9"/><path d="M92 42 L116 42 L103 66 Z" fill="#d9262b"/><text x="54" y="50" text-anchor="middle" font-family="Archivo Black,sans-serif" font-size="25" fill="#0f2c59">Step</text><text x="54" y="82" text-anchor="middle" font-family="Archivo Black,sans-serif" font-size="25" fill="#0f2c59">2</text></svg>
        Fill out your vehicle &amp; driver information.
      </div>
      <div class="step" style="left:313px">
        <svg width="118" height="108" viewBox="0 0 118 108"><circle cx="54" cy="54" r="51" fill="#fff" stroke="#d9262b" stroke-width="2"/><path d="M54 3 A51 51 0 0 1 104 44" fill="none" stroke="#d9262b" stroke-width="9"/><path d="M92 42 L116 42 L103 66 Z" fill="#d9262b"/><text x="54" y="50" text-anchor="middle" font-family="Archivo Black,sans-serif" font-size="25" fill="#0f2c59">Step</text><text x="54" y="82" text-anchor="middle" font-family="Archivo Black,sans-serif" font-size="25" fill="#0f2c59">3</text></svg>
        Compare rates &amp; <span class="save">save!</span>
      </div>
    </div>

    <form class="zip-form" action="http://www.brightpolicysaver.example/index1178.php?subid=8715815" method="get">
      <div class="zip-box">
        <svg width="402" height="95" style="position:absolute;left:0;top:0"><path d="M78 0 H326 Q336 0 336 10 V34 H394 Q402 34 402 42 V87 Q402 95 394 95 H8 Q0 95 0 87 V42 Q0 34 8 34 H68 V10 Q68 0 78 0 Z" fill="#d3d8db"/></svg>
        <label class="zip-label" for="zip">Enter your zip code here!</label>
        <input class="zip-input" id="zip" name="zip" type="text" inputmode="numeric">
      </div>
      <button class="continue-btn" type="submit">Continue
        <svg width="24" height="24" viewBox="0 0 24 24"><circle cx="12" cy="12" r="11" fill="#fff"/><path d="M9 6 L17 12 L9 18 Z" fill="#c41e23"/></svg>
      </button>
    </form>
    <div class="secure-note">Your Information is Secure
      <svg width="11" height="12" viewBox="0 0 11 12" style="vertical-align:-1px"><path d="M2.5 5 V3.5 a3 3 0 0 1 6 0 V5" fill="none" stroke="#c9a227" stroke-width="1.5"/><rect x="1" y="5" width="9" height="7" rx="1" fill="#e3b52f"/></svg>
    </div>
    <div class="trust-badge"></div>
  </div>
</section>

<section class="legal">
  <p style="top:20px">BrightPolicySaver.example is a top savings referral service which enables consumers to quickly and easily request multiple competitive insurance quotes from local insurance agents and companies. Our site does not provide quotes directly to consumers. We do not provide insurance and we do not represent any specific insurance provider.</p>
  <p style="top:61px">The lowest advertised rates are not necessarily available from all advertisers on our site. BrightPolicySaver.example matches users to advertisers and insurance agents only after we've received certain information from you, and your rates may vary based on your coverage limits, deductibles, driving history, education, occupation, type of vehicle, and location, among other factors.</p>
  <p style="top:113px">This offer is not available to residents of Minnesota</p>
</section>

<footer class="site-footer">
  <div class="footer-links">
    <a href="#">Home</a> &nbsp;|&nbsp; <a href="#">Privacy Policy</a> &nbsp;|&nbsp; <a href="#">Terms of Use</a><br>
    Copyright © 2012 BrightPolicySaver.example All Rights Reserved.
  </div>
  <div class="footer-badge"></div>
</footer>
</body>
</html>
```